New Business Card for Web Design/Internet Marketing Company

Looking for a great looking new business card. We are a 10 year old web design, internet marketing and website management company that works mostly with small businesses.

Our new card needs to better match the colors and style of our website, be bold, extremely usable and slightly edgy.

Target Market(s)

Small/Medium businesses that have websites

Industry/Entity Type

Internet

Requirements
Must have
• Front and back design, full color, rounded corners please

Must use the colors/style of our website (JPG provided)

INFO FOR CARDS (as readable as possible please)
Mark Lenner
President/CEO
mark@trelvanmedia.example
Phone: 520-381-7459
Toll Free: 866-381-7459
Address: 4315 W. Calloway Ave. Ste. 140, Tucson, AZ 85792

THINGS I WANT TO PROMOTE (if there is room):
1. Our Website - www.trelvanmedia.example

2. Social Media
Twitter: @trelvanmedia
Facebook: www.facebook.com/trelvanmedia

3. Our Services
Web Design
Internet Marketing
Website Management

```html
<!DOCTYPE html>
<html lang="en">
<head>
<meta charset="utf-8">
<title>Trelvan Media – Business Card</title>
<link href="https://fonts.googleapis.com/css2?family=Source+Sans+3:wght@400;600;700&display=swap" rel="stylesheet">
<style>
  :root {
    --stage: #ececec;
    --card: #ffffff;
    --card-edge: #d6d6d6;
    --brand-blue: #1a8fc4;
    --brand-orange: #f08a35;
    --ink: #4a4a4a;
    --rule: #c9c9c9;
  }
  * { margin: 0; padding: 0; box-sizing: border-box; }
  html, body { width: 1200px; height: 410px; overflow: hidden; }
  body {
    background: var(--stage);
    font-family: "Source Sans 3", "Myriad Pro", Arial, sans-serif;
    color: var(--ink);
    position: relative;
  }
  .card {
    position: absolute;
    top: 56px;
    width: 524px;
    height: 299px;
    background: var(--card);
    border: 1px solid var(--card-edge);
    border-radius: 6px;
  }
  .card--front { left: 57px; }
  .card--back { left: 622px; }

  .brand {
    position: absolute;
    display: flex;
    align-items: center;
    gap: 10px;
    font-weight: 700;
    color: var(--brand-blue);
    white-space: nowrap;
  }
  .brand__dot {
    border-radius: 50%;
    background: var(--brand-orange);
    flex: none;
  }
  .card--front .brand { left: 22px; top: 160px; font-size: 34px; }
  .card--front .brand__dot { width: 22px; height: 22px; }
  .card--back .brand { left: 0; right: 0; top: 74px; justify-content: center; font-size: 46px; }
  .card--back .brand__dot { width: 28px; height: 28px; }

  .divider {
    position: absolute;
    left: 275px;
    top: 62px;
    width: 1px;
    height: 178px;
    background: var(--rule);
  }
  .person {
    position: absolute;
    left: 296px;
    top: 70px;
    font-size: 16.5px;
    white-space: nowrap;
  }
  .person__name { color: var(--brand-orange); font-weight: 700; }
  .person__title { color: var(--brand-blue); font-size: 14.5px; }

  .contacts {
    position: absolute;
    left: 296px;
    top: 108px;
    list-style: none;
    font-size: 13.5px;
    line-height: 19px;
  }
  .contacts li { display: flex; align-items: center; gap: 6px; white-space: nowrap; }
  .contacts svg { width: 11px; height: 11px; fill: var(--ink); flex: none; }

  .address {
    position: absolute;
    left: 296px;
    top: 197px;
    font-size: 13.5px;
    line-height: 18px;
    font-style: normal;
  }

  .services {
    position: absolute;
    left: 0; right: 0;
    top: 180px;
    text-align: center;
    list-style: none;
    font-size: 17px;
    font-weight: 700;
    color: var(--brand-blue);
    line-height: 23px;
  }
  .services li { display: inline-block; margin: 0 6px; }
  .services li::before {
    content: "";
    display: inline-block;
    width: 8px; height: 8px;
    border-radius: 50%;
    background: var(--brand-orange);
    margin-right: 7px;
    vertical-align: 2px;
  }
  .social {
    position: absolute;
    left: 0; right: 0;
    top: 252px;
    display: flex;
    justify-content: center;
    gap: 14px;
    list-style: none;
    font-size: 17px;
  }
  .social li { display: flex; align-items: center; gap: 5px; }
  .social__mark { width: 13px; height: 13px; background: var(--brand-blue); border-radius: 2px; }
</style>
</head>
<body>
  <section class="card card--front">
    <div class="brand"><span class="brand__dot"></span>Trelvan Media</div>
    <div class="divider"></div>
    <p class="person"><span class="person__name">Mark Lenner ,</span> <span class="person__title">President/CEO</span></p>
    <ul class="contacts">
      <li><svg viewBox="0 0 24 24"><path d="M6.6 10.8a15.1 15.1 0 0 0 6.6 6.6l2.2-2.2a1 1 0 0 1 1-.25 11.4 11.4 0 0 0 3.6.57 1 1 0 0 1 1 1V20a1 1 0 0 1-1 1A17 17 0 0 1 3 4a1 1 0 0 1 1-1h3.5a1 1 0 0 1 1 1c0 1.25.2 2.45.57 3.57a1 1 0 0 1-.25 1z"/></svg>866-381-7459</li>
      <li><svg viewBox="0 0 24 24"><path d="M6.6 10.8a15.1 15.1 0 0 0 6.6 6.6l2.2-2.2a1 1 0 0 1 1-.25 11.4 11.4 0 0 0 3.6.57 1 1 0 0 1 1 1V20a1 1 0 0 1-1 1A17 17 0 0 1 3 4a1 1 0 0 1 1-1h3.5a1 1 0 0 1 1 1c0 1.25.2 2.45.57 3.57a1 1 0 0 1-.25 1z"/></svg>520-381-7459</li>
      <li><svg viewBox="0 0 24 24"><path d="M2 5h20v14H2z M3.5 6.5 12 13l8.5-6.5" fill="none" stroke="#4a4a4a" stroke-width="2.4"/></svg>mark@trelvanmedia.example</li>
      <li><svg viewBox="0 0 24 24"><circle cx="12" cy="12" r="10"/><path d="M2 12h20M12 2c3 3 3 17 0 20M12 2c-3 3-3 17 0 20" fill="none" stroke="#fff" stroke-width="1.5"/></svg>www.trelvanmedia.example</li>
    </ul>
    <address class="address">4315 W. Calloway Ave. Ste. 140<br>Tucson, AZ 85792</address>
  </section>

  <section class="card card--back">
    <div class="brand"><span class="brand__dot"></span>Trelvan Media</div>
    <ul class="services">
      <li>Web Design</li><li>Internet Marketing</li><br><li>Website Management</li>
    </ul>
    <ul class="social">
      <li><span class="social__mark"></span>@trelvanmedia</li>
      <li><span class="social__mark"></span>trelvanmedia</li>
    </ul>
  </section>
</body>
</html>
```